Redgum Ridge Towing website

We need a website design for a towing company based in Australia.
The design should be simple and minimalist. The site can be in colours of the logo are Blue, Red and White (see attached) - but we'd like to see options in some sort of industrial looking metallic theme if possible.
We base our business on our friendly and efficient customer service, the design should attempt to convey this in some way.

```html
<!DOCTYPE html>
<html lang="en">
<head>
<meta charset="utf-8">
<title>Redgum Ridge Towing</title>
<link href="https://fonts.googleapis.com/css2?family=Arimo:wght@400;700&family=Source+Sans+3:wght@400;600&display=swap" rel="stylesheet">
<style>
  :root {
    --backdrop: #2a2a2a;
    --page: #ffffff;
    --nav-top: #0f3f8a;
    --nav-bottom: #062a63;
    --nav-active: #1a57ad;
    --red: #d9141b;
    --text: #4a4a4a;
    --muted: #666666;
    --link: #2460b3;
    --panel: #f1f1f1;
    --line: #cfcfcf;
    --footer: #2b2b2b;
  }
  * { box-sizing: border-box; margin: 0; padding: 0; }
  html, body { width: 847px; height: 1200px; overflow: hidden; }
  body {
    background: radial-gradient(ellipse at 50% 30%, #3a3a3a, var(--backdrop) 70%);
    font-family: "Arimo", Arial, sans-serif;
    color: var(--text);
    position: relative;
  }
  .page { position: absolute; left: 82px; top: 60px; width: 679px; height: 1098px; background: var(--page); }
  .abs { position: absolute; }

  .brand { left: 39px; top: 22px; display: flex; align-items: center; gap: 7px; }
  .brand-mark { width: 16px; height: 16px; background: var(--nav-top); }
  .brand-name { font-family: "Source Sans 3", sans-serif; font-weight: 600; font-size: 15px; color: var(--nav-top); width: 90px; line-height: 1.1; }

  .contact-line { top: 27px; font-family: "Source Sans 3", sans-serif; font-size: 11px; color: #444; display: flex; align-items: center; gap: 6px; }
  .contact-phone { left: 420px; }
  .contact-mail { left: 522px; }

  .search { left: 489px; top: 65px; width: 153px; height: 21px; border: 1px solid var(--line); font-family: "Source Sans 3", sans-serif; font-size: 9px; color: #777; padding: 4px 8px; }
  .search svg { position: absolute; right: 6px; top: 5px; }

  .nav { left: 39px; top: 110px; width: 604px; height: 33px; background: linear-gradient(var(--nav-top), var(--nav-bottom)); display: flex; }
  .nav a { display: block; height: 33px; line-height: 33px; font-family: "Source Sans 3", sans-serif; font-size: 10.5px; color: #fff; text-decoration: none; text-align: center; border-right: 1px solid rgba(255,255,255,0.12); }
  .nav a.active { background: var(--nav-active); }

  .hero { left: 39px; top: 143px; width: 604px; height: 279px; background: linear-gradient(180deg, #6f7a64 0%, #8f9788 35%, #5d6368 65%, #2f3133 100%); }
  .hero-caption { position: absolute; left: 1px; top: 163px; width: 365px; height: 80px; background: rgba(60,60,60,0.6); padding: 14px 0 0 43px; color: #fff; }
  .hero-caption h1 { font-weight: 400; font-size: 17px; letter-spacing: 0.2px; margin-bottom: 5px; }
  .hero-caption p { font-size: 9.5px; line-height: 1.55; }
  .hero-dots { position: absolute; left: 561px; top: 263px; display: flex; gap: 2px; }
  .hero-dots span { width: 6px; height: 6px; border-radius: 50%; background: #333; border: 1px solid #eee; }
  .hero-dots span.on { background: #fff; border-color: #888; }

  .service { top: 460px; width: 182px; }
  .service .photo { width: 182px; height: 98px; border: 4px solid #fff; box-shadow: 0 0 2px rgba(0,0,0,0.45); }
  .service h2 { font-weight: 400; font-size: 12px; color: var(--red); margin-top: 16px; }
  .service p { font-size: 8.3px; line-height: 14px; color: var(--muted); margin-top: 6px; }
  .btn-more { display: block; margin: 9px 0 0 auto; width: 62px; height: 19px; background: var(--red); color: #fff; font-size: 8.5px; line-height: 19px; text-align: center; }

  .section-title { font-weight: 400; font-size: 15px; color: var(--red); }
  .welcome-title { left: 39px; top: 714px; }
  .welcome-photo { left: 39px; top: 747px; width: 146px; height: 97px; background: linear-gradient(135deg, #5a5650 0%, #3c3c3c 35%, #1f4fa5 60%, #d97a1a 100%); }
  .welcome-text { left: 204px; top: 745px; width: 186px; font-size: 8.6px; line-height: 14.8px; color: var(--muted); }
  .news-title { left: 39px; top: 866px; }
  .news { left: 39px; top: 899px; width: 360px; list-style: none; }
  .news li { position: relative; padding-left: 16px; font-family: "Source Sans 3", sans-serif; font-size: 8.8px; line-height: 12.5px; color: var(--muted); margin-bottom: 8px; }
  .news li::before { content: ""; position: absolute; left: 2px; top: 2px; width: 5px; height: 5px; border-radius: 50%; border: 2px solid #fff; background: #666; box-shadow: 0 0 0 1px #777; }
  .news-more { left: 360px; top: 982px; font-family: "Source Sans 3", sans-serif; font-size: 9px; color: var(--link); }

  .quick { left: 446px; top: 716px; width: 197px; height: 276px; background: var(--panel); border: 1px solid #e3e3e3; }
  .quick h3 { font-weight: 400; font-size: 15px; color: var(--red); text-align: center; margin-top: 15px; }
  .field { position: absolute; left: 10px; width: 178px; height: 25px; background: #fff; border: 1px solid var(--line); font-family: "Source Sans 3", sans-serif; font-size: 9px; color: #666; padding: 6px 9px; }
  .submit { position: absolute; left: 32px; top: 234px; width: 140px; height: 29px; background: var(--red); border-bottom: 2px solid #a50e13; color: #fff; font-family: "Source Sans 3", sans-serif; font-size: 12px; text-align: center; line-height: 28px; }

  .footer { left: 0; top: 1025px; width: 679px; height: 73px; background: var(--footer); color: #eee; font-size: 8.3px; }
  .footer-links { position: absolute; left: 39px; top: 22px; }
  .footer-copy { position: absolute; left: 39px; top: 42px; }
  .social { position: absolute; top: 21px; width: 22px; height: 22px; }
</style>
</head>
<body>
  <div class="page">
    <div class="abs brand">
      <span class="brand-mark"></span>
      <span class="brand-name">Redgum Ridge Towing</span>
    </div>

    <div class="abs contact-line contact-phone">
      <svg width="9" height="12" viewBox="0 0 9 12"><path d="M7 1 C3 2 1 6 3 11 L5 10 C4 7 5 5 7 4 Z" fill="#444"/></svg>
      903-555-0147
    </div>
    <div class="abs contact-line contact-mail">
      <svg width="13" height="9" viewBox="0 0 13 9"><rect x="0.5" y="0.5" width="12" height="8" fill="none" stroke="#444"/><path d="M0.5 0.5 L6.5 5 L12.5 0.5" fill="none" stroke="#444"/></svg>
      hello@redgumridge.example
    </div>

    <div class="abs search">Search..
      <svg width="9" height="9" viewBox="0 0 9 9"><circle cx="3.7" cy="3.7" r="2.8" fill="none" stroke="#888" stroke-width="1.2"/><path d="M5.8 5.8 L8.5 8.5" stroke="#888" stroke-width="1.3"/></svg>
    </div>

    <nav class="abs nav">
      <a class="active" style="width:66px">HOME</a>
      <a style="width:86px">ABOUT US</a>
      <a style="width:81px">SERVICES</a>
      <a style="width:106px">TESTIMONIALS</a>
      <a style="width:99px">CONTACT US</a>
    </nav>

    <div class="abs hero" role="img" aria-label="Silver sports car being loaded onto a flatbed tow truck in a suburban driveway">
      <div class="hero-caption">
        <h1>DUIS AUTEM VEL EUM IRURE DOLOR</h1>
        <p>Jerta baditaut onsequser untur magni dolores eioquie voluptate msei nesciunt. Voluptatem accusantium dolorem lorem. consuetudium.</p>
      </div>
      <div class="hero-dots"><span class="on"></span><span></span><span></span><span></span></div>
    </div>

    <div class="abs service" style="left:39px">
      <div class="photo" role="img" aria-label="Red tow truck hooking up a car on a roadside" style="background:linear-gradient(135deg,#6f9a5a,#b52a2a 55%,#8a8a8a)"></div>
      <h2>Local Towing</h2>
      <p>Claritas est etiam processus dynamicus, qui seqi uitur mutationem consuetudium lecitorum.Miru es t notare quam littera gothica, quam. Claritas.</p>
      <span class="btn-more">READ MORE</span>
    </div>
    <div class="abs service" style="left:251px">
      <div class="photo" role="img" aria-label="Car carrier transporting vehicles along a country highway" style="background:linear-gradient(160deg,#4f7a3e,#9aa39c 55%,#d0d2d0)"></div>
      <h2>Long Distance Towing</h2>
      <p>Claritas est etiam processus dynamicus, qui seqi uitur mutationem consuetudium lecitorum.Miru es t notare quam littera gothica, quam. Claritas.</p>
      <span class="btn-more">READ MORE</span>
    </div>
    <div class="abs service" style="left:461px">
      <div class="photo" role="img" aria-label="Heavy duty wrecker towing a semi truck on the road" style="background:linear-gradient(160deg,#8a8d88,#c9cbc8 55%,#6d6f6c)"></div>
      <h2>Heavy Duty Towing</h2>
      <p>Claritas est etiam processus dynamicus, qui seqi uitur mutationem consuetudium lecitorum.Miru es t notare quam littera gothica, quam. Claritas.</p>
      <span class="btn-more">READ MORE</span>
    </div>

    <h2 class="abs section-title welcome-title">Welcome to Redgum Ridge Towing</h2>
    <div class="abs welcome-photo" role="img" aria-label="Towing chains, hooks and a blue winch"></div>
    <p class="abs welcome-text">Duis autem vel euim iriure dolor in hendrerit in vulputate velit esse molestie consequat, vel illu m dolore eu feugiat nulla facilisis at vero eros et accumsan et iusto odio dignissim qui blandit pr aesent luptatum zzril delenit augue duis dolore te feugait nulla facilisi. Nam liber tempor cum s oluta nobis eleifend option congue.</p>

    <h2 class="abs section-title news-title">Latest News</h2>
    <ul class="abs news">
      <li>Established in 1986 with 25 years of outstanding service, a State approved vendor</li>
      <li>A Service-Disabled Veteran-Owned company focused on hiring Service Disabled Veterans, Veterans and family members of veterans</li>
      <li>As a member of the National Green Works Council, we support green design, construction and operations</li>
    </ul>
    <span class="abs news-more">More..</span>

    <div class="abs quick">
      <h3>Quick contact</h3>
      <div class="field" style="top:46px">Name</div>
      <div class="field" style="top:82px">Phone</div>
      <div class="field" style="top:118px">E-mail</div>
      <div class="field" style="top:153px;height:67px">Message</div>
      <div class="submit">Submit Request</div>
    </div>

    <footer class="abs footer">
      <div class="footer-links">Home | About us | Services | Testimonials | Contact us</div>
      <div class="footer-copy">Copyrights 2013. All Rights Reserved.</div>
      <span class="social" style="left:507px;background:#3b5998"></span>
      <span class="social" style="left:536px;background:#2a9fd6"></span>
      <span class="social" style="left:564px;background:#f26f21"></span>
      <span class="social" style="left:594px;background:#d42a2a"></span>
    </footer>
  </div>
</body>
</html>
```